Orvane Mechanical - Letterhead

We are a plumbing and hvac company based in Calgary. This letterhead will be on our quotes, invoices, preventative maintenance proposals etc.

```html
<!DOCTYPE html>
<html lang="en">
<head>
<meta charset="utf-8">
<title>Orvane Mechanical – Letterhead</title>
<link href="https://fonts.googleapis.com/css2?family=Montserrat:ital,wght@0,400;0,600;0,700;1,600;1,700&family=Work+Sans:wght@400&display=swap" rel="stylesheet">
<style>
  :root {
    --backdrop: #e9e7e4;
    --paper: #ffffff;
    --brand-blue: #2470b8;
    --brand-orange: #ee5a26;
    --ink-strong: #4a4a4c;
    --ink-body: #6d6d70;
    --ink-contact: #2b2b2d;
    --mark-tint: #fbe6de;
  }
  * { box-sizing: border-box; margin: 0; padding: 0; }
  html, body { width: 1185px; height: 1200px; overflow: hidden; background: var(--backdrop); }
  .letterhead {
    position: absolute; left: 182px; top: 20px;
    width: 820px; height: 1160px;
    background: var(--paper);
    overflow: hidden;
    font-family: "Montserrat", sans-serif;
  }
  .brand {
    position: absolute; left: 0; right: 0; top: 130px;
    display: flex; justify-content: center; align-items: center; gap: 10px;
  }
  .brand-dot { width: 14px; height: 14px; border-radius: 50%; background: var(--brand-orange); }
  .brand-name { font-size: 26px; font-weight: 700; color: var(--brand-blue); letter-spacing: 0.5px; }
  .backdrop-mark {
    position: absolute; left: 420px; top: 870px;
    width: 420px; height: 420px; border-radius: 50%;
    background: var(--mark-tint);
  }
  .salutation {
    position: absolute; left: 79px; top: 264px;
    font-size: 20px; font-weight: 600; color: var(--ink-strong);
  }
  .letter-body {
    position: absolute; left: 79px; top: 318px; width: 663px;
    font-size: 11.6px; line-height: 20.7px; color: var(--ink-body);
    text-align: justify;
  }
  .letter-body p + p { margin-top: 28px; }
  .sign-off { position: absolute; left: 79px; top: 818px; }
  .signer-name { font-size: 21px; font-weight: 700; font-style: italic; color: var(--ink-strong); line-height: 1.1; }
  .signer-role { font-size: 11px; font-weight: 600; font-style: italic; color: var(--ink-contact); }
  .signature {
    position: absolute; left: 79px; top: 889px; width: 212px; height: 66px;
    background: linear-gradient(90deg, #f2f2f2, #e6e6e6);
    border-radius: 4px;
  }
  .footer-rule {
    position: absolute; left: 79px; top: 1039px; width: 663px; height: 1.5px;
    background: var(--brand-orange);
  }
  .contact-list, .address {
    position: absolute; top: 1072px;
    font-family: "Work Sans", sans-serif; font-size: 12.4px; line-height: 16.6px; color: var(--ink-contact);
    list-style: none;
  }
  .contact-list { left: 79px; }
  .contact-list li { display: flex; align-items: center; gap: 6px; }
  .contact-list svg { width: 8px; height: 8px; }
  .address { right: 78px; top: 1089px; text-align: right; }
  .footer-band { position: absolute; left: 0; top: 1144px; width: 820px; height: 16px; }
</style>
</head>
<body>
<main class="letterhead">
  <div class="backdrop-mark" aria-hidden="true"></div>

  <header class="brand">
    <span class="brand-dot"></span>
    <span class="brand-name">ORVANE MECHANICAL</span>
  </header>

  <h1 class="salutation">Dear sir/Madam,</h1>

  <section class="letter-body">
    <p>Lorem Ipsum is simply dummy text of the printing and typesetting industry. Lorem Ipsum has been the industry's standard dummy text ever since the 1500s, when an unknown printer took a galley of type and scrambled it to make a type specimen book. It has survived not only five centuries, but also the leap into electronic typesetting, remaining essentially unchanged. It was popularised in the 1960s with the release of Typeset</p>
    <p>of type and scrambled it to make a type specimen book. It has survived not only five centuries, but also the leap into electronic typesetting, remaining essentially unchanged. It was popularised in the 1960s with the release of Typeset sheets containing Lorem Ipsum passages, and more recently with desktop publishing software like</p>
    <p>Contrary to popular belief, Lorem Ipsum is not simply random text. It has roots in a piece of classical Latin literature from 45 BC, making it over 2000 years old. Adrian Fellowes, a Latin professor at Harrowgate College in Vermont, looked up one of the more obscure Latin words, consectetur, from a Lorem Ipsum passage, and going through the cites of the word in classical literature, discovered the undoubtable source. Lorem Ipsum comes from sections 1.10.32 and 1.10.33 of "de Finibus Bonorum et Malorum" (The Extremes of Good and Evil), written in 45 BC. This book is a treatise on the theory of ethics, very popular during the Renaissance. The first line of Lorem Ipsum, "Lorem ipsum dolor sit amet..", comes from a line in section 1.10.32. typesetting, remaining essentially unchanged. It was popularised in the 1960s with the release of Typeset sheets containing Lorem Ipsum passages, and more recently with desktop publishing software like Folio Page There are many variations of passages of Lorem Ipsum available, but the majority have suffered alteration in</p>
    <p>some form, by injected humour, or randomised words which don't look even slightly believable. If you are going to use a passage of Lorem Ipsum, you need to be sure there isn't anything embarrassing hidden in the middle</p>
  </section>

  <div class="sign-off">
    <p class="signer-name">Dana Whitlock</p>
    <p class="signer-role">Director</p>
  </div>
  <div class="signature" role="img" aria-label="Handwritten signature of Dana Whitlock"></div>

  <div class="footer-rule"></div>

  <ul class="contact-list">
    <li><svg viewBox="0 0 8 8"><path d="M1.5 0.5 L3 0.5 L3.4 2.4 L2.5 3 Q3.2 4.6 5 5.5 L5.6 4.6 L7.5 5 L7.5 6.5 Q4 7.5 1.5 4.5 Q0.6 2.5 1.5 0.5Z" fill="var(--brand-blue)"/></svg>(403) 555-0142</li>
    <li><svg viewBox="0 0 8 8"><rect x="0.5" y="1.5" width="7" height="5" fill="none" stroke="var(--brand-blue)"/><path d="M0.5 1.5 L4 4.5 L7.5 1.5" fill="none" stroke="var(--brand-blue)"/></svg>info@orvanemech.com</li>
    <li><svg viewBox="0 0 8 8"><circle cx="4" cy="4" r="3.4" fill="none" stroke="var(--brand-blue)"/><path d="M0.6 4 H7.4 M4 0.6 V7.4" stroke="var(--brand-blue)" stroke-width="0.7"/></svg>www.orvanemech.com</li>
  </ul>
  <p class="address">2215 Kestrel Road<br>Calgary, AB T2P 0K4</p>

  <svg class="footer-band" viewBox="0 0 820 16" preserveAspectRatio="none" aria-hidden="true">
    <polygon points="0,2 419,2 399,16 0,16" fill="var(--brand-blue)"/>
    <polygon points="426,0 820,0 820,16 406,16" fill="var(--brand-orange)"/>
  </svg>
</main>
</body>
</html>
```